Meridale Nutrition needs Stationary and a business card

We would like to use our current logo. The text can be moved around as needed. The stationary needs to be a 'first page' where the logo is more prominent to be impressive on higher quality paper and a second page where the logo is more subtle where there will be much more information on the page. There are 2 clinic locations which will need include name, address, phone number, fax number, web address. The business card should be single sided and contain this information also.
The design must be contemporary and sophisticated as this is a science based diet run out of a medical clinic.

Target Market(s)

People wanting to lose weight, athletes looking to optimise performance, people with arthritis or fighting cancer

Industry/Entity Type

Business

Contact Information for Business Card

must use the logo. I have attached an example card with the practice details on it. there must be space for the doctors name. Also the website www.meridalenutrition.com.au

Requirements
Must have
• the logo, the business adresses and phone numbers, the website, the doctors name and qualifications
Nice to have
• some creativity
Should not have
• Do not simply reproduce the existing card please

```html
<!DOCTYPE html>
<html lang="en">
<head>
<meta charset="utf-8">
<title>Meridale Nutrition – Stationery</title>
<link href="https://fonts.googleapis.com/css2?family=Questrial&family=Mulish:wght@400;700&display=swap" rel="stylesheet">
<style>
  :root {
    --backdrop: #d1d2d4;
    --navy: #33679a;
    --sky: #36c3f1;
    --paper: #ffffff;
    --shadow: rgba(0, 0, 0, 0.45);
  }
  html, body {
    margin: 0;
    padding: 0;
    width: 1200px;
    height: 927px;
    overflow: hidden;
    background: var(--backdrop);
  }
  .stage {
    position: relative;
    width: 1200px;
    height: 927px;
  }
  .sheet {
    position: absolute;
    top: 142px;
    width: 496px;
    height: 641px;
    overflow: hidden;
    box-shadow: 6px 8px 10px var(--shadow);
  }
  .sheet svg {
    display: block;
    width: 100%;
    height: 100%;
  }
  .sheet--letterhead { left: 89px; background: var(--paper); }
  .sheet--cover { left: 615px; background: var(--navy); }
  .wordmark {
    font-family: "Questrial", sans-serif;
    fill: var(--paper);
    letter-spacing: 0.5px;
  }
  .contact {
    font-family: "Mulish", sans-serif;
    font-size: 10px;
  }
  .contact--dark { fill: var(--navy); }
  .contact--light { fill: var(--paper); }
  .contact__label { font-weight: 700; font-size: 11px; }
</style>
</head>
<body>
<main class="stage">

  <section class="sheet sheet--letterhead" aria-label="Letterhead">
    <svg viewBox="0 0 535 692" preserveAspectRatio="none">
      <!-- header waves -->
      <path class="header-wave" fill="var(--sky)" d="M0,30 V82 C40,97 100,100 150,90 C230,72 290,32 330,0 H0 Z"/>
      <path class="header-band" fill="var(--navy)" d="M0,0 H320 C260,35 190,70 110,78 C60,82 20,72 0,58 Z"/>
      <text class="wordmark" x="21" y="34" font-size="22">MERIDALE NUTRITION</text>

      <!-- corner mark -->
      <circle class="corner-mark" cx="476" cy="52" r="38" fill="var(--sky)" stroke="var(--navy)" stroke-width="3"/>

      <!-- footer waves -->
      <path class="footer-wave" fill="var(--sky)" d="M225,692 C310,640 420,592 535,618 V692 Z"/>
      <path class="footer-band" fill="var(--navy)" d="M215,692 C320,662 430,628 535,648 V692 Z"/>

      <!-- footer contacts -->
      <g class="contact contact--dark">
        <text class="contact__label" x="21" y="652">Ashby</text>
        <text x="21" y="665">52-54 Kellerman Road</text>
        <text x="21" y="678">Ashby NSW 2138</text>
        <text x="130" y="652"><tspan class="contact__label">T:</tspan> 02 9511 3847</text>
        <text x="130" y="665">Shoulder and Elbow</text>
        <text x="130" y="680" font-size="11">www.ashbyortho.com.au</text>
      </g>
      <g class="contact contact--light" text-anchor="end">
        <text x="406" y="652"><tspan class="contact__label">F:</tspan> 02 9488 6120</text>
        <text x="406" y="665">Knee Surgery</text>
        <text x="406" y="680" font-size="11">www.jointclinic.com.au</text>
        <text class="contact__label" x="515" y="655">Linfield</text>
        <text x="515" y="668">214 Harwood Road</text>
        <text x="515" y="681">Linfield NSW 2034</text>
      </g>
    </svg>
  </section>

  <section class="sheet sheet--cover" aria-label="Cover page">
    <svg viewBox="0 0 535 692" preserveAspectRatio="none">
      <!-- top waves -->
      <path class="cover-wave-edge" fill="var(--paper)" d="M210,0 H535 V96 C470,102 400,86 330,56 C280,32 240,12 210,0 Z"/>
      <path class="cover-wave" fill="var(--sky)" d="M218,0 H535 V72 C480,96 420,90 352,62 C292,36 252,15 218,0 Z"/>

      <text class="wordmark" x="268" y="225" font-size="38" text-anchor="middle">MERIDALE NUTRITION</text>

      <!-- bottom waves -->
      <path class="cover-wave-edge" fill="var(--paper)" d="M0,692 V640 C30,600 100,595 170,620 C230,642 280,670 320,692 Z"/>
      <path class="cover-wave" fill="var(--sky)" d="M0,692 V665 C40,625 110,622 170,640 C220,655 260,675 290,692 Z"/>

      <!-- feature circle -->
      <circle class="cover-disc" cx="369" cy="527" r="160" fill="var(--sky)" stroke="var(--paper)" stroke-width="8"/>
    </svg>
  </section>

</main>
</body>
</html>
```